Corvel Creamery Works ( Australian Dairy site )

We need a new website we are a new company in Australia manufacturing dairy products ( Packing Butter ) We want to have a new modern punchy website with the basic details of the company and company certifications should be linked in a pdf etc.. maybe photos of the site modernised graphics etc.. we need to show our customers our brand clean and green image of Australian high quality products packed under strict Australian quality standards.

Target Market(s)

export - Asia

Industry/Entity Type

It Company

Number of Pages Required

5+ page

Requirements
Must have
• Home page
• About us page
• Products page
• Contact us page
• Facility / Accreditations ( Under facility pdf files eg Licenses, halal etc.. )

```html
<!DOCTYPE html>
<html lang="en">
<head>
<meta charset="utf-8">
<title>Corvel Creamery Works</title>
<link href="https://fonts.googleapis.com/css2?family=Hind:wght@400;500;600&family=Open+Sans:wght@400;600;700&display=swap" rel="stylesheet">
<style>
:root{
  --green:#3a9d2f;
  --green-dark:#2a8a24;
  --green-light:#55b947;
  --yellow:#f5b800;
  --yellow-light:#ffc61a;
  --ink:#444;
  --muted:#777;
  --panel:#f1f2f4;
  --line:#e2e2e2;
  --white:#fff;
}
*{margin:0;padding:0;box-sizing:border-box}
html,body{width:1200px;height:2341px;overflow:hidden}
body{position:relative;font-family:"Open Sans",Arial,sans-serif;color:var(--ink);background:var(--white)}
.abs{position:absolute}
.topbar{left:0;top:0;width:1200px;height:48px;background:var(--yellow);color:var(--white);font-size:12.5px;display:flex;justify-content:center;align-items:center;gap:46px}
.topbar span{display:flex;align-items:center;gap:8px}
.header{left:0;top:48px;width:1200px;height:97px;background:var(--white)}
.brand{left:86px;top:26px;display:flex;align-items:center;gap:12px}
.brand-dot{width:44px;height:44px;border-radius:50%;background:var(--green)}
.brand-name{font-family:"Hind",sans-serif;font-weight:600;font-size:21px;line-height:22px;color:var(--green);width:170px}
.nav{left:0;top:0;width:1200px;height:97px;font-family:"Hind",sans-serif;font-size:13px;letter-spacing:.3px;color:#555}
.nav a{position:absolute;top:40px;transform:translateX(-50%);color:inherit;text-decoration:none;white-space:nowrap;line-height:18px}
.nav a.active{top:24px;background:var(--yellow);color:var(--white);width:68px;height:50px;border-radius:50% 40% 50% 40%;display:flex;align-items:center;justify-content:center}
.round-btn{width:38px;height:38px;border:2px solid var(--green);border-radius:50%;top:30px;display:flex;align-items:center;justify-content:center}
.hero{left:0;top:145px;width:1200px;height:581px;background:linear-gradient(180deg,#2f86d8 0%,#7fbbef 38%,#cfe6f6 52%,#8bbf3a 56%,#5ea124 100%)}
.hero-curve{left:0;top:616px}
.dots{left:1148px;top:350px;display:flex;flex-direction:column;gap:7px}
.dots i{width:12px;height:12px;border:2px solid var(--white);border-radius:50%;display:block}
.dots i.on{background:var(--green)}
.section-title{font-family:"Hind",sans-serif;font-weight:600;font-size:22px;letter-spacing:.6px;color:var(--green);display:flex;align-items:center;gap:12px;white-space:nowrap}
.section-title em{font-style:normal;color:var(--yellow)}
.title-dot{width:30px;height:30px;border-radius:50%;background:var(--green)}
.intro{left:240px;top:818px;width:720px;text-align:center;font-size:12.5px;line-height:24px;color:#555}
.feature{top:905px;width:240px;text-align:center}
.feature-icon{width:120px;height:82px;margin:0 auto;border-radius:55% 45% 55% 45%/60% 50% 50% 40%;background:var(--green);box-shadow:0 6px 0 var(--yellow)}
.feature-icon.alt{background:var(--yellow);box-shadow:0 6px 0 var(--green)}
.feature h3{margin-top:22px;font-size:12.5px;font-weight:600;color:#333;letter-spacing:.3px}
.feature p{margin:12px auto 0;width:222px;font-size:12.5px;line-height:24px;color:var(--muted)}
.products{left:0;top:1155px;width:1200px;height:445px;background:var(--panel);border-top:2px solid var(--green)}
.tab{left:462px;top:1155px;width:300px;height:52px;background:var(--green);color:var(--white);border-radius:0 0 60px 60px;font-family:"Hind",sans-serif;font-weight:600;font-size:22px;letter-spacing:.6px;display:flex;align-items:center;justify-content:center}
.card{top:1242px;width:238px;height:306px;background:var(--white);border:1px solid var(--line);text-align:center}
.card-img{margin:6px;height:182px;background:radial-gradient(ellipse at center,#fafafa 0%,#e9e9ea 100%)}
.card h3{margin-top:26px;font-size:12.5px;font-weight:600;color:#444;letter-spacing:.3px}
.card p{margin:10px 22px 0;font-size:12.5px;line-height:20px;color:var(--muted)}
.facility-text{left:86px;top:1706px;width:330px;font-size:12.5px;line-height:22px;color:#444}
.checklist{left:86px;top:1796px;width:340px;list-style:none;font-size:12.5px;color:#555}
.checklist li{display:flex;gap:12px;line-height:21px;margin-bottom:12px}
.checklist svg{flex:none;margin-top:3px}
.cert{left:488px;top:1712px;width:192px;height:262px;border:1px solid var(--line);background:linear-gradient(160deg,#ffffff 0%,#f1f3f5 100%)}
.accred{left:713px;top:1714px;width:400px}
.accred h4{font-size:15px;font-weight:400;color:var(--yellow);margin-bottom:16px}
.accred p{font-size:12.5px;line-height:23.5px;color:#444;margin-bottom:14px}
.arrows{left:1084px;top:1650px;font-size:14px;color:#999;letter-spacing:12px}
.footer{left:0;top:2024px;width:1200px;height:248px;background:linear-gradient(180deg,var(--green-light) 0%,var(--green-dark) 100%);color:var(--white)}
.foot-brand{left:118px;top:44px;width:200px;text-align:center}
.foot-dot{width:150px;height:110px;border-radius:50%;background:var(--white);margin:0 auto 14px}
.foot-brand div.name{font-family:"Hind",sans-serif;font-weight:600;font-size:26px;line-height:28px}
.foot-col h3{font-family:"Hind",sans-serif;font-weight:500;font-size:22px;margin-bottom:22px}
.foot-col{top:38px;font-size:12px;line-height:18px}
.contact-list{list-style:none}
.contact-list li{display:flex;gap:14px;margin-bottom:12px}
.contact-list a{color:var(--white)}
.email-field{margin-top:16px;width:237px;height:35px;background:var(--white);color:#666;padding:9px 14px;font-size:12px}
.subscribe{margin-top:9px;width:80px;height:28px;background:var(--yellow);color:var(--white);font-size:11px;font-weight:600;display:flex;align-items:center;justify-content:center}
.socials{display:flex;gap:8px;margin-top:16px}
.socials i{width:36px;height:36px;border:1.5px solid var(--white);border-radius:50%;display:block}
.copybar{left:0;top:2272px;width:1200px;height:69px;background:linear-gradient(180deg,var(--yellow-light),var(--yellow));color:var(--white);font-size:12px;display:flex;align-items:center;justify-content:center}
</style>
</head>
<body>

<div class="abs topbar">
  <span><svg width="12" height="12" viewBox="0 0 24 24" fill="#fff"><path d="M6.6 10.8a15 15 0 0 0 6.6 6.6l2.2-2.2c.3-.3.7-.4 1-.2 1.1.4 2.3.6 3.6.6.6 0 1 .4 1 1V20c0 .6-.4 1-1 1A17 17 0 0 1 3 4c0-.6.4-1 1-1h3.5c.6 0 1 .4 1 1 0 1.3.2 2.5.6 3.6.1.3 0 .7-.2 1z"/></svg>CALL US : +61 3 9188 2604</span>
  <span><svg width="13" height="11" viewBox="0 0 24 18" fill="none" stroke="#fff" stroke-width="2"><rect x="1" y="1" width="22" height="16"/><path d="M1 1l11 9 11-9"/></svg>EMAIL : info@corvelcreamery.com.au</span>
  <span><svg width="10" height="13" viewBox="0 0 20 26" fill="#fff"><path d="M10 0a10 10 0 0 0-10 10c0 7 10 16 10 16s10-9 10-16A10 10 0 0 0 10 0zm0 14a4 4 0 1 1 0-8 4 4 0 0 1 0 8z"/></svg>ADDRESS : 18 Harlow Lane, Kealba, Victoria 3021 Australia</span>
</div>

<header class="abs header">
  <div class="abs brand"><span class="brand-dot"></span><span class="brand-name">Corvel Creamery Works</span></div>
  <nav class="abs nav">
    <a class="active" href="#" style="left:457px">HOME</a>
    <a href="#" style="left:544px">ABOUT US</a>
    <a href="#" style="left:643px">PRODUCTS</a>
    <a href="#" style="left:739px">FACILITY</a>
    <a href="#" style="left:854px">ACCREDITATIONS</a>
    <a href="#" style="left:980px">CONTACT US</a>
  </nav>
  <div class="abs round-btn" style="left:1033px;border-color:var(--yellow)"><svg width="18" height="16" viewBox="0 0 24 20" fill="none" stroke="#f5b800" stroke-width="2"><path d="M1 1h4l3 12h12l3-9H7"/><circle cx="10" cy="17" r="1.5"/><circle cx="18" cy="17" r="1.5"/></svg></div>
  <div class="abs round-btn" style="left:1076px"><svg width="14" height="14" viewBox="0 0 20 20" fill="none" stroke="#3a9d2f" stroke-width="2.5"><circle cx="8" cy="8" r="6"/><path d="M13 13l5 5"/></svg></div>
</header>

<div class="abs hero" role="img" aria-label="Photograph of a dairy cow in a green pasture with grazing herd and packs of butter in the foreground"></div>
<svg class="abs hero-curve" width="1200" height="115" viewBox="0 0 1200 115" preserveAspectRatio="none">
  <path d="M0 20 Q420 120 1200 30 L1200 115 L0 115 Z" fill="#f5b800"/>
  <path d="M0 26 Q430 128 1200 48 L1200 115 L0 115 Z" fill="#3a9d2f"/>
  <path d="M0 48 Q450 136 1200 60 L1200 115 L0 115 Z" fill="#fff"/>
</svg>
<div class="abs dots"><i></i><i></i><i class="on"></i><i></i><i></i></div>

<h2 class="abs section-title" style="left:368px;top:766px"><span class="title-dot"></span><span>WELCOME TO <em>CORVEL CREAMERY</em></span></h2>
<p class="abs intro">Sed ut perspiciatis unde omnis iste natus error sit voluptatem accusantium doloremque laudantium, totam rem aperiam, eaque ipsa quae ab illo inventore veritatis et quasi architecto beatae vitae dicta sunt explicabo.</p>

<div class="abs feature" style="left:83px"><div class="feature-icon alt" role="img" aria-label="Cow icon"></div><h3>CONTRARY TO POPULAR</h3><p>Sed ut perspiciatis unde omnis iste natus error sit voluptatem accusantium beatae vitae dicta sunt explicabo.</p></div>
<div class="abs feature" style="left:348px"><div class="feature-icon" role="img" aria-label="Milk churn icon"></div><h3>CONTRARY TO POPULAR</h3><p>Sed ut perspiciatis unde omnis iste natus error sit voluptatem accusantium beatae vitae dicta sunt explicabo.</p></div>
<div class="abs feature" style="left:609px"><div class="feature-icon" role="img" aria-label="Cream separator icon"></div><h3>CONTRARY TO POPULAR</h3><p>Sed ut perspiciatis unde omnis iste natus error sit voluptatem accusantium beatae vitae dicta sunt explicabo.</p></div>
<div class="abs feature" style="left:868px"><div class="feature-icon" role="img" aria-label="Butter bowl icon"></div><h3>CONTRARY TO POPULAR</h3><p>Sed ut perspiciatis unde omnis iste natus error sit voluptatem accusantium beatae vitae dicta sunt explicabo.</p></div>

<section class="abs products"></section>
<div class="abs tab">LATEST PRODUCTS</div>
<div class="abs card" style="left:86px"><div class="card-img" role="img" aria-label="Blue butter block pack"></div><h3>CONTRARY TO POPULAR</h3><p>Sed ut perspiciatis unde omnis iste vitae dicta sunt explicabo.</p></div>
<div class="abs card" style="left:349px"><div class="card-img" role="img" aria-label="Red butter portion tub"></div><h3>CONTRARY TO POPULAR</h3><p>Sed ut perspiciatis unde omnis iste vitae dicta sunt explicabo.</p></div>
<div class="abs card" style="left:612px"><div class="card-img" role="img" aria-label="Red salted butter block pack"></div><h3>CONTRARY TO POPULAR</h3><p>Sed ut perspiciatis unde omnis iste vitae dicta sunt explicabo.</p></div>
<div class="abs card" style="left:876px"><div class="card-img" role="img" aria-label="Blue butter block pack"></div><h3>CONTRARY TO POPULAR</h3><p>Sed ut perspiciatis unde omnis iste vitae dicta sunt explicabo.</p></div>

<h2 class="abs section-title" style="left:86px;top:1643px"><span class="title-dot"></span><span>OUR <em>FACILITY</em></span></h2>
<p class="abs facility-text">Sed ut perspiciatis unde omnis iste natus error sit voluptatem accusantium doloremque laudantium, totam rem ,bea tae vitae dicta sunt explicabo.</p>
<ul class="abs checklist">
  <li><svg width="13" height="13" viewBox="0 0 20 20"><circle cx="10" cy="10" r="8.5" fill="none" stroke="#3a9d2f" stroke-width="2"/><path d="M6 10l3 3 5-6" fill="none" stroke="#3a9d2f" stroke-width="2.2"/></svg>Natural butter, no artificial colours, additives, preser vatives or hormone</li>
  <li><svg width="13" height="13" viewBox="0 0 20 20"><circle cx="10" cy="10" r="8.5" fill="none" stroke="#3a9d2f" stroke-width="2"/><path d="M6 10l3 3 5-6" fill="none" stroke="#3a9d2f" stroke-width="2.2"/></svg>Vegetarian Friendly</li>
  <li><svg width="13" height="13" viewBox="0 0 20 20"><circle cx="10" cy="10" r="8.5" fill="none" stroke="#3a9d2f" stroke-width="2"/><path d="M6 10l3 3 5-6" fill="none" stroke="#3a9d2f" stroke-width="2.2"/></svg>Australian Owned</li>
  <li><svg width="13" height="13" viewBox="0 0 20 20"><circle cx="10" cy="10" r="8.5" fill="none" stroke="#3a9d2f" stroke-width="2"/><path d="M6 10l3 3 5-6" fill="none" stroke="#3a9d2f" stroke-width="2.2"/></svg>Packed in Australia understrict food safety standards</li>
  <li><svg width="13" height="13" viewBox="0 0 20 20"><circle cx="10" cy="10" r="8.5" fill="none" stroke="#3a9d2f" stroke-width="2"/><path d="M6 10l3 3 5-6" fill="none" stroke="#3a9d2f" stroke-width="2.2"/></svg>Halal Certified</li>
</ul>

<h2 class="abs section-title" style="left:490px;top:1643px"><span class="title-dot"></span><span>OUR <em>ACCREDITATIONS</em></span></h2>
<div class="abs arrows">‹›</div>
<div class="abs cert" role="img" aria-label="Dairy manufacturer licence certificate document"></div>
<div class="abs accred">
  <h4>Neque porro quisquam est qui dolorem ipsum</h4>
  <p>Sed ut perspiciatis unde omnis iste natus error sit voluptatem accusantium doloremque laudantium, totam rem aperiam, eaque ipsa quae ab illo inventore veritatis et quasi architecto beatae vitae dicta sunt explicabo. Nemo enim ipsam voluptatem quia voluptas sit aspernatur aut odit aut fugit, sed quia consequuntur magni dolores eos qui ratione voluptatem sequi nesciunt.</p>
  <p>Nemo enim ipsam voluptatem quia voluptas sit aspernatur aut odit aut fugit, sed quia consequuntur magni dolores eos qui ratione voluptatem accusantium doloremque laudantiums equi nesciunt.</p>
</div>

<footer class="abs footer">
  <div class="abs foot-brand"><div class="foot-dot"></div><div class="name">Corvel Creamery Works</div></div>
  <div class="abs foot-col" style="left:370px;width:220px">
    <h3>Contact Us</h3>
    <ul class="contact-list">
      <li><svg width="12" height="12" viewBox="0 0 24 24" fill="#fff"><path d="M6.6 10.8a15 15 0 0 0 6.6 6.6l2.2-2.2c.3-.3.7-.4 1-.2 1.1.4 2.3.6 3.6.6.6 0 1 .4 1 1V20c0 .6-.4 1-1 1A17 17 0 0 1 3 4c0-.6.4-1 1-1h3.5c.6 0 1 .4 1 1 0 1.3.2 2.5.6 3.6.1.3 0 .7-.2 1z"/></svg>+61 3 9188 2604 (Phone)</li>
      <li><svg width="12" height="12" viewBox="0 0 24 24" fill="#fff"><rect x="5" y="2" width="14" height="7"/><rect x="2" y="9" width="20" height="9" rx="1"/><rect x="6" y="15" width="12" height="7"/></svg>+61 3 9188 2604 (Fax)</li>
      <li><svg width="12" height="10" viewBox="0 0 24 18" fill="#fff"><path d="M0 0h24v3l-12 8L0 3z"/><path d="M0 5l12 8 12-8v13H0z"/></svg><a href="#">info@corvelcreamery.com.au</a></li>
      <li><svg width="10" height="13" viewBox="0 0 20 26" fill="#fff"><path d="M10 0a10 10 0 0 0-10 10c0 7 10 16 10 16s10-9 10-16A10 10 0 0 0 10 0zm0 14a4 4 0 1 1 0-8 4 4 0 0 1 0 8z"/></svg>18 Harlow Lane, Kealba,<br>Victoria 3021 Australia</li>
    </ul>
  </div>
  <div class="abs foot-col" style="left:620px;width:240px">
    <h3>Newsletter Signup</h3>
    <p>Register Your email address to get information about us</p>
    <div class="email-field">Email Address</div>
    <div class="subscribe">SUBSCRIBE</div>
  </div>
  <div class="abs foot-col" style="left:907px;width:200px">
    <h3>Follow Us</h3>
    <p>Lorem ipsum dolor sit amet, conse ctetur adipiscing elit. Nulla in purus nibh. Donec ornare</p>
    <div class="socials" aria-label="Social media links"><i></i><i></i><i></i><i></i><i></i></div>
  </div>
</footer>
<div class="abs copybar">© Copyright 2016 Corvel Creamery.All Rights Reserved</div>

</body>
</html>
```